Brightmill Data Works

Our company is about IT hardwares and IT solutions. IT hardware such as PC, RAMS, storage and servers. IT solutions such as project management, BA. We are also selling new technology too.

Target Market(s)

Consumer, Small to Medium Business, Corporate

Requirements
Must have
• The business card must have the following:
• Name:
• Title:
• Contact Number:
• Email address:
• Website:
• Color: Must match the logo color upgrade

```html
<!DOCTYPE html>
<html lang="en">
<head>
<meta charset="utf-8">
<title>Brightmill Data Works – Business Card</title>
<link rel="stylesheet" href="https://fonts.googleapis.com/css2?family=Saira:wght@700&family=Open+Sans:wght@400;600&display=swap">
<style>
  :root {
    --backdrop: #262626;
    --card-dark: #3a3a3c;
    --card-dark-edge: #2f2f31;
    --card-light: #f4f4f4;
    --ink-dark: #3b3b3d;
    --ink-light: #d9d9d9;
    --accent: #c98a2e;
    --band: #3d3d3f;
    --contact-text: #ececec;
  }
  * { margin: 0; padding: 0; box-sizing: border-box; }
  html, body {
    width: 1200px; height: 997px; overflow: hidden;
    background: var(--backdrop);
  }
  .stage { position: relative; width: 1200px; height: 997px; }

  .card {
    position: absolute; left: 280px;
    width: 640px; height: 366px;
    border-radius: 18px; overflow: hidden;
    box-shadow: 0 14px 34px rgba(0,0,0,.45);
  }

  /* Back of card */
  .card--back { top: 80px; background: linear-gradient(135deg, var(--card-dark), var(--card-dark-edge)); }
  .brand-mark {
    position: absolute; left: 50%; top: 50%; transform: translate(-50%, -50%);
    display: flex; align-items: center; gap: 22px;
  }
  .brand-dot { width: 40px; height: 40px; border-radius: 50%; background: var(--accent); flex: none; }
  .brand-name {
    font-family: "Saira", sans-serif; font-weight: 700;
    font-size: 40px; line-height: 1.05; letter-spacing: 1px;
    color: var(--ink-light); text-transform: uppercase; white-space: nowrap;
  }
  .brand-name span { display: block; }

  /* Front of card */
  .card--front { top: 530px; background: var(--card-light); }
  .card-art { position: absolute; inset: 0; }
  .front-name {
    position: absolute; left: 0; right: 0; top: 44px; text-align: center;
    font-family: "Saira", sans-serif; font-weight: 700;
    font-size: 46px; line-height: 1.05; letter-spacing: 1px;
    color: var(--ink-dark); text-transform: uppercase; white-space: nowrap;
  }
  .front-name span { display: block; }
  .holder {
    position: absolute; left: 110px; top: 286px; text-align: left;
    font-family: "Open Sans", sans-serif;
  }
  .holder-name { font-size: 17px; font-weight: 400; color: var(--accent); text-transform: uppercase; }
  .holder-title { font-size: 13px; font-weight: 600; color: var(--contact-text); margin-top: 2px; }
  .divider {
    position: absolute; left: 318px; top: 256px; width: 2px; height: 84px;
    background: var(--accent);
  }
  .contacts {
    position: absolute; left: 340px; top: 256px; list-style: none;
    font-family: "Open Sans", sans-serif; font-size: 14px; color: var(--contact-text);
  }
  .contacts li { display: flex; align-items: center; gap: 10px; height: 28px; }
  .contact-icon { width: 18px; height: 18px; flex: none; }
</style>
</head>
<body>
<main class="stage">

  <section class="card card--back" aria-label="Card back">
    <div class="brand-mark">
      <span class="brand-dot"></span>
      <p class="brand-name"><span>Brightmill</span><span>Data Works</span></p>
    </div>
  </section>

  <section class="card card--front" aria-label="Card front">
    <svg class="card-art" viewBox="0 0 640 366" width="640" height="366" aria-hidden="true">
      <path d="M0,300 C170,235 420,205 640,215 L640,366 L0,366 Z" fill="var(--band)"/>
      <path d="M30,292 C200,215 430,180 620,186" fill="none" stroke="var(--accent)" stroke-width="4" stroke-linecap="round"/>
    </svg>

    <h1 class="front-name"><span>Brightmill</span><span>Data Works</span></h1>

    <div class="holder">
      <p class="holder-name">Daniel Reyes</p>
      <p class="holder-title">Managing Director</p>
    </div>

    <span class="divider"></span>

    <ul class="contacts">
      <li>
        <svg class="contact-icon" viewBox="0 0 18 18" aria-hidden="true">
          <circle cx="9" cy="9" r="8" fill="none" stroke="var(--accent)" stroke-width="1.5"/>
          <path d="M5 7.5 Q9 4 13 7.5 L12 9 L10 8.3 L10 7 Q9 6.6 8 7 L8 8.3 L6 9 Z" fill="var(--accent)"/>
          <rect x="6" y="10" width="6" height="3" rx="1" fill="var(--accent)"/>
        </svg>
        <span>9410 3385</span>
      </li>
      <li>
        <svg class="contact-icon" viewBox="0 0 18 18" aria-hidden="true">
          <circle cx="9" cy="9" r="8" fill="none" stroke="var(--accent)" stroke-width="1.5"/>
          <rect x="4.5" y="6" width="9" height="6" rx="1" fill="var(--accent)"/>
          <path d="M4.8 6.3 L9 9.5 L13.2 6.3" fill="none" stroke="var(--band)" stroke-width="1"/>
        </svg>
        <span>dreyes@brightmilldata.com</span>
      </li>
      <li>
        <svg class="contact-icon" viewBox="0 0 18 18" aria-hidden="true">
          <circle cx="9" cy="9" r="8" fill="none" stroke="var(--accent)" stroke-width="1.5"/>
          <circle cx="9" cy="9" r="4.5" fill="none" stroke="var(--accent)" stroke-width="1"/>
          <ellipse cx="9" cy="9" rx="2" ry="4.5" fill="none" stroke="var(--accent)" stroke-width="1"/>
          <path d="M4.5 9 H13.5" stroke="var(--accent)" stroke-width="1"/>
        </svg>
        <span>www.brightmilldata.com</span>
      </li>
    </ul>
  </section>

</main>
</body>
</html>
```